Website design for legal tech start up in Switzerland (B2B)

We are for a legal tech start up in Switzerland called KOVA. We have been running since August 2016. This will be our first live website.

We need a website designed and business card design for our start-up in Switzerland. We also need the Web design to be converted into HTML and CSS files.

Function of website:
• To inform potential customers of our services
• Form a key part of our digital marketing and sales footprint.
• Branding

Please find attached logo.
Updates

Project Deadline Extended Reason: Giving us time to review submissions and provide opportunity for more submissions. Added Thursday, February 16, 2017

Project Deadline Extended
Reason: Looking for more idea's not necessarily set on blue and grey colours only.

Target Market(s)

B2B tech powered legal services.

Industry/Entity Type

Legal

Contact Information for Business Card

Lean and slick design.

Coding

Coded - Design and coding required

Number of Pages Required

5+ page

Requirements
Must have
• VERY LEAN AND CLEAN DESIGN!
• We have received many great standard designs, but we are looking for something more out-of-the box: You can get inspiration from these designs: http://www.pixelvane.com/websites/clean/
• Thanks!!
• Easy content management system
• Well structured coding for additional development
• Responsive webpage for all types of devices
• SEO optimized
• Tabs (Home, services, team, careers, blog, contact us)
• Colour scheme complementary to logo
Nice to have
• Look and Design - Approachable, High-tech, Modern
• Easy to add chat bot capability in future
Should not have
• Too busy/ too much clutter
• Not take to long to load

```html
<!DOCTYPE html>
<html lang="en">
<head>
<meta charset="utf-8">
<title>KOVA – Legal Services</title>
<link rel="stylesheet" href="https://fonts.googleapis.com/css2?family=Open+Sans:wght@400;600;700&display=swap">
<style>
:root{
  --navy:#13325f;
  --navy-deep:#1d3a6b;
  --text:#333;
  --muted:#8a8a8a;
  --rule:#cfcfcf;
  --band:#f4f4f4;
  --footer:#464646;
  --footer-bottom:#3f3f3f;
  --footer-text:#d8d8d8;
  --white:#fff;
}
*{box-sizing:border-box;margin:0;padding:0}
html,body{width:1200px;height:2452px;overflow:hidden}
body{font-family:"Open Sans",Arial,sans-serif;color:var(--text);background:var(--white);position:relative}
.wrap{position:absolute;left:132px;width:936px}

/* header */
.site-header{position:absolute;top:0;left:0;width:1200px;height:110px;background:var(--white)}
.brand{position:absolute;left:132px;top:28px;font-size:52px;font-weight:700;color:#3d4656;letter-spacing:2px;line-height:1}
.main-nav{position:absolute;right:132px;top:47px;display:flex;gap:27px;font-size:12px;letter-spacing:.3px}
.main-nav a{color:#555;text-decoration:none}
.main-nav a.active{color:var(--navy)}

/* hero */
.hero{position:absolute;top:110px;left:0;width:1200px;height:503px;overflow:hidden;
  background:linear-gradient(180deg,#6f9bd3 0%,#a9c6e8 35%,#dfe7f0 60%,#9fb2c8 100%)}
.hero-overlay{position:absolute;inset:0}
.hero-contact{position:absolute;left:132px;top:145px;width:241px}
.hero-contact h2{color:var(--white);font-size:24px;font-weight:700;margin-bottom:10px}
.field{display:block;width:241px;height:42px;background:var(--white);border:0;margin-bottom:17px;padding-left:24px;font:12px "Open Sans",sans-serif;color:#777;line-height:42px}
.btn-submit{display:block;width:80px;height:44px;background:#1c1c1c;color:var(--white);font-size:13px;font-weight:600;line-height:44px;text-align:center;margin-top:2px}
.slide-arrow{position:absolute;top:232px;width:24px;height:32px;background:#1f2632}
.slide-arrow.prev{left:0}.slide-arrow.next{right:0}

/* generic section */
.section-title{text-align:center;font-size:24px;font-weight:700;color:var(--navy);letter-spacing:.3px}
.btn-outline{display:inline-block;border:1px solid var(--rule);color:#555;font-size:12px;text-align:center;background:var(--white)}

/* welcome */
.welcome{position:absolute;top:613px;left:0;width:1200px;height:330px}
.welcome .section-title{position:absolute;top:74px;width:1200px}
.welcome p{position:absolute;top:114px;left:132px;width:936px;font-size:12px;line-height:19.6px;color:#666;text-align:justify}
.welcome .btn-outline{position:absolute;top:214px;left:556px;width:88px;height:38px;line-height:36px}

/* services */
.services{position:absolute;top:943px;left:0;width:1200px;height:407px;background:var(--band)}
.services .section-title{position:absolute;top:72px;width:1200px}
.service{position:absolute;top:140px;width:220px;text-align:center}
.service svg{display:block;margin:0 auto;height:46px}
.service h3{font-size:21px;font-weight:400;color:var(--navy);margin-top:10px;line-height:26px}
.service p{font-size:10.5px;line-height:16px;color:#666;margin-top:3px}
.service .btn-outline{width:82px;height:37px;line-height:35px;font-size:10px;margin-top:14px}

/* team */
.team{position:absolute;top:1350px;left:0;width:1200px;height:303px}
.team .section-title{position:absolute;top:72px;width:1200px}
.member{position:absolute;top:130px;width:440px;height:95px}
.member .photo{position:absolute;left:0;top:0;width:95px;height:95px;background:linear-gradient(160deg,#c9b9a6,#7f766f)}
.member h3{position:absolute;left:108px;top:-4px;font-size:16px;font-weight:400;color:#222;letter-spacing:.5px}
.member .role{position:absolute;left:108px;top:24px;font-size:11px;color:#333}
.member p{position:absolute;left:108px;top:50px;width:330px;font-size:10.5px;line-height:16.5px;color:#888;text-align:justify}
.member p b{font-weight:400;color:#222}

/* blog */
.blog{position:absolute;top:1653px;left:0;width:1200px;height:526px;background:var(--band)}
.blog h2{position:absolute;left:132px;top:64px;font-size:24px;font-weight:700;color:var(--navy)}
.carousel-nav{position:absolute;right:132px;top:71px;display:flex;gap:4px}
.carousel-nav span{width:22px;height:22px;border:1px solid #aaa;background:var(--white)}
.post{position:absolute;top:116px;width:298px}
.post .thumb{width:298px;height:180px;position:relative}
.post h3{font-size:14.5px;font-weight:400;color:#222;line-height:21px;margin-top:14px}
.post p{font-size:10.5px;line-height:16px;color:#999;text-align:justify;margin-top:7px}
.post .meta{display:flex;gap:18px;font-size:10.5px;color:#666;margin-top:16px;align-items:center}
.post .meta span{display:flex;align-items:center;gap:5px}

/* footer */
.site-footer{position:absolute;top:2179px;left:0;width:1200px;height:211px;background:var(--footer);color:var(--footer-text)}
.site-footer h4{font-size:16px;font-weight:400;color:var(--white)}
.contact-info{position:absolute;left:132px;top:42px}
.contact-info ul{list-style:none;margin-top:12px;font-size:10.5px;line-height:16px}
.contact-info li{display:flex;gap:12px;margin-bottom:6px}
.contact-info svg{flex:none;margin-top:3px}
.map{position:absolute;left:332px;top:76px;width:185px;height:99px;background:linear-gradient(135deg,#eeeeee,#d9d9d9)}
.footer-links{position:absolute;left:646px;top:42px}
.footer-links .cols{display:flex;gap:40px;margin-top:12px}
.footer-links ul{list-style:none;font-size:10.5px;line-height:22px}
.footer-links li::before{content:"•";margin-right:7px}
.social{position:absolute;left:973px;top:42px}
.social .icons{display:flex;flex-wrap:wrap;width:60px;gap:6px;margin-top:14px}
.social .icons span{width:24px;height:24px;border-radius:50%;background:#6c7a91}
.footer-bottom{position:absolute;top:2390px;left:0;width:1200px;height:62px;background:var(--footer-bottom);border-top:1px solid #555;text-align:center;font-size:10.5px;color:#ccc;line-height:62px}
</style>
</head>
<body>

<header class="site-header">
  <div class="brand">KOVA</div>
  <nav class="main-nav">
    <a class="active" href="#">HOME</a><a href="#">SERVICES</a><a href="#">TEAM</a><a href="#">CAREERS</a><a href="#">BLOG</a><a href="#">CONTACT US</a>
  </nav>
</header>

<section class="hero" role="img" aria-label="Snow-covered alpine mountain peaks under a blue sky with clouds">
  <svg class="hero-overlay" width="1200" height="503" viewBox="0 0 1200 503" aria-hidden="true">
    <polygon points="0,0 409,0 597,283 433,503 0,503" fill="#1f4683" fill-opacity=".72"/>
  </svg>
  <span class="slide-arrow prev"></span>
  <span class="slide-arrow next"></span>
  <form class="hero-contact">
    <h2>CONTACT US</h2>
    <span class="field">Email</span>
    <span class="field">What is your legal question</span>
    <span class="btn-submit">SUBMIT</span>
  </form>
</section>

<section class="welcome">
  <h2 class="section-title">WELCOME TO KOVA</h2>
  <p>Donec facilisis volutpat lorem, at euismod velit dignissim ac. Class aptent taciti sociosqu ad litora torquent per conubia nostra, per inceptos himenaeos. Nulla consequat ipsum id mi placerat viverra. Sed tempor ex id dui sagittis, at luctus tortor finibus. Vestibulum ante ipsum primis in faucibus orci luctus et ultrices posuere cubilia Curae; Duis varius condimentum tellus, a faucibus lorem vestibulum eu. Duis sit amet tellus nisl. Maecenas nec metus sodales ante sollicitudin auctor in quis velit. Maecenas libero nisi, dignissim eget nibh a, mollis eleifend tellus. Fusce maximus porttitor libero vitae viverra.</p>
  <span class="btn-outline">Read more</span>
</section>

<section class="services">
  <h2 class="section-title">OUR SERVICES</h2>
  <div class="service" style="left:127px">
    <svg viewBox="0 0 46 46" width="46"><circle cx="23" cy="10" r="6" fill="var(--navy-deep)"/><circle cx="10" cy="15" r="5" fill="var(--navy-deep)"/><circle cx="36" cy="15" r="5" fill="var(--navy-deep)"/><path d="M13 42v-12a10 10 0 0 1 20 0v12z" fill="var(--navy-deep)"/><path d="M2 38v-8a8 8 0 0 1 11-7v15zM44 38v-8a8 8 0 0 0-11-7v15z" fill="var(--navy-deep)"/></svg>
    <h3>FAMILY LAW</h3>
    <p>Duis varius ate condimentum tellus, faucibus lorem vestibulum eu. Duis sit amet tellus nisl. Maecenas nec metus sodales.</p>
    <span class="btn-outline">READ MORE</span>
  </div>
  <div class="service" style="left:369px">
    <svg viewBox="0 0 46 46" width="46"><path d="M17 12v-4h12v4" fill="none" stroke="var(--navy-deep)" stroke-width="3"/><rect x="3" y="12" width="40" height="28" rx="3" fill="var(--navy-deep)"/><rect x="3" y="23" width="40" height="2" fill="#fff"/><rect x="20" y="21" width="6" height="6" fill="#fff"/></svg>
    <h3>BUSINESS LAW</h3>
    <p>Duis varius ate condimentum tellus, faucibus lorem vestibulum eu. Duis sit amet tellus nisl. Maecenas nec metus sodales.</p>
    <span class="btn-outline">READ MORE</span>
  </div>
  <div class="service" style="left:611px">
    <svg viewBox="0 0 50 46" width="50"><path d="M9 20l5-11h22l5 11z" fill="var(--navy-deep)"/><rect x="3" y="20" width="44" height="14" rx="4" fill="var(--navy-deep)"/><rect x="7" y="32" width="8" height="9" rx="2" fill="var(--navy-deep)"/><rect x="35" y="32" width="8" height="9" rx="2" fill="var(--navy-deep)"/><path d="M15 18l3-6h14l3 6z" fill="#fff"/><circle cx="11" cy="27" r="3" fill="#fff"/><circle cx="39" cy="27" r="3" fill="#fff"/></svg>
    <h3>VEHICLE LAW</h3>
    <p>Duis varius ate condimentum tellus, faucibus lorem vestibulum eu. Duis sit amet tellus nisl. Maecenas nec metus sodales.</p>
    <span class="btn-outline">READ MORE</span>
  </div>
  <div class="service" style="left:853px">
    <svg viewBox="0 0 54 46" width="54"><rect x="2" y="9" width="50" height="30" fill="var(--navy-deep)"/><rect x="7" y="14" width="40" height="20" fill="#fff"/><circle cx="27" cy="24" r="8" fill="var(--navy-deep)"/><path d="M25 20h3v9h-3z" fill="#fff"/></svg>
    <h3>DEBT LAW</h3>
    <p>Duis varius ate condimentum tellus, faucibus lorem vestibulum eu. Duis sit amet tellus nisl. Maecenas nec metus sodales.</p>
    <span class="btn-outline">READ MORE</span>
  </div>
</section>

<section class="team">
  <h2 class="section-title">OUR TEAM</h2>
  <article class="member" style="left:132px">
    <div class="photo" role="img" aria-label="Portrait photo of team member Marc Keller"></div>
    <h3>MARC KELLER</h3>
    <div class="role">Duis sed congue nibh</div>
    <p>Aenean lobortis neque, vitae faucibus lorem. Nulla dignissim tempus nisi, sed lobortis velit faucibus at. Fusce vel rutrum erat. Vivamus blandit interdum egestas. <b>More</b></p>
  </article>
  <article class="member" style="left:629px">
    <div class="photo" role="img" aria-label="Portrait photo of team member Lena" style="background:linear-gradient(160deg,#d9c3a8,#a88a6a)"></div>
    <h3>LENA</h3>
    <div class="role">Duis sed congue nibh</div>
    <p>Aenean lobortis neque, vitae faucibus lorem. Nulla dignissim tempus nisi, sed lobortis velit faucibus at. Fusce vel rutrum erat. Vivamus blandit interdum egestas. <b>More</b></p>
  </article>
</section>

<section class="blog">
  <h2>BLOG</h2>
  <div class="carousel-nav"><span></span><span></span></div>

  <article class="post" style="left:132px">
    <div class="thumb" role="img" aria-label="Columned courthouse facade under a cloudy sky" style="background:linear-gradient(180deg,#7d8fad,#5c6577 60%,#3f4550)"></div>
    <h3>Donec scelerisque felis at ante rhoncus, non mattis nulla facilisis</h3>
    <p>Integer gravida risus risus, in imperdiet leo convallis sed. Aenean lobortis neque, vitae faucibus lorem. Nulla dignissim tempus nisi, sed lobortis velit faucibus at. Fusce vel rutrum erat. Vivamus blandit interdum egestas.</p>
    <div class="meta">
      <span><svg width="11" height="10" viewBox="0 0 11 10"><path d="M5.5 10L1 5.5A2.6 2.6 0 0 1 5.5 1.8 2.6 2.6 0 0 1 10 5.5z" fill="#555"/></svg>(28)</span>
      <span><svg width="10" height="10" viewBox="0 0 10 10"><rect x="0" y="4" width="2.5" height="6" fill="#555"/><path d="M3.5 4l2-4h1v3.5H10V6l-1.5 4h-5z" fill="#555"/></svg>(21)</span>
      <span><svg width="10" height="10" viewBox="0 0 10 10"><rect x=".5" y="1.5" width="9" height="8" fill="none" stroke="#555"/><rect x=".5" y="1.5" width="9" height="2" fill="#555"/></svg>8 Feb, 2017</span>
    </div>
  </article>

  <article class="post" style="left:451px">
    <div class="thumb" role="img" aria-label="Person in a suit stamping a document beside a small justice statue" style="background:linear-gradient(135deg,#2e3440,#c9cdd3 55%,#f0f0f0)"></div>
    <h3>Donec scelerisque felis at ante rhoncus, non mattis nulla facilisis</h3>
    <p>Integer gravida risus risus, in imperdiet leo convallis sed. Aenean lobortis neque, vitae faucibus lorem. Nulla dignissim tempus nisi, sed lobortis velit faucibus at. Fusce vel rutrum erat. Vivamus blandit interdum egestas.</p>
    <div class="meta">
      <span><svg width="11" height="10" viewBox="0 0 11 10"><path d="M5.5 10L1 5.5A2.6 2.6 0 0 1 5.5 1.8 2.6 2.6 0 0 1 10 5.5z" fill="#555"/></svg>(28)</span>
      <span><svg width="10" height="10" viewBox="0 0 10 10"><rect x="0" y="4" width="2.5" height="6" fill="#555"/><path d="M3.5 4l2-4h1v3.5H10V6l-1.5 4h-5z" fill="#555"/></svg>(21)</span>
      <span><svg width="10" height="10" viewBox="0 0 10 10"><rect x=".5" y="1.5" width="9" height="8" fill="none" stroke="#555"/><rect x=".5" y="1.5" width="9" height="2" fill="#555"/></svg>8 Feb, 2017</span>
    </div>
  </article>

  <article class="post" style="left:770px">
    <div class="thumb" role="img" aria-label="Video still of an old town riverside at dusk" style="background:linear-gradient(180deg,#6f7f93,#8a6e55 50%,#3f4a45)">
      <svg width="40" height="40" viewBox="0 0 40 40" style="position:absolute;left:129px;top:70px"><circle cx="20" cy="20" r="20" fill="#fff"/><path d="M15 11l14 9-14 9z" fill="#222"/></svg>
    </div>
    <h3>Donec scelerisque felis at ante rhoncus, non mattis nulla facilisis</h3>
    <p>Integer gravida risus risus, in imperdiet leo convallis sed. Aenean lobortis neque, vitae faucibus lorem. Nulla dignissim tempus nisi, sed lobortis velit faucibus at. Fusce vel rutrum erat. Vivamus blandit interdum egestas.</p>
    <div class="meta">
      <span><svg width="11" height="10" viewBox="0 0 11 10"><path d="M5.5 10L1 5.5A2.6 2.6 0 0 1 5.5 1.8 2.6 2.6 0 0 1 10 5.5z" fill="#555"/></svg>(28)</span>
      <span><svg width="10" height="10" viewBox="0 0 10 10"><rect x="0" y="4" width="2.5" height="6" fill="#555"/><path d="M3.5 4l2-4h1v3.5H10V6l-1.5 4h-5z" fill="#555"/></svg>(21)</span>
      <span><svg width="10" height="10" viewBox="0 0 10 10"><rect x=".5" y="1.5" width="9" height="8" fill="none" stroke="#555"/><rect x=".5" y="1.5" width="9" height="2" fill="#555"/></svg>8 Feb, 2017</span>
    </div>
  </article>
</section>

<footer class="site-footer">
  <div class="contact-info">
    <h4>Contact info</h4>
    <ul>
      <li><svg width="8" height="11" viewBox="0 0 8 11"><path d="M4 11L.6 5.5A3.6 3.6 0 1 1 7.4 5.5z" fill="#ccc"/><circle cx="4" cy="3.8" r="1.3" fill="#464646"/></svg><span>24 Building name, Street name<br>City - Zipcode</span></li>
      <li><svg width="8" height="11" viewBox="0 0 8 11"><rect x=".5" y=".5" width="7" height="10" rx="1" fill="#ccc"/><rect x="2" y="2" width="4" height="6" fill="#464646"/></svg><span>555 210 4837</span></li>
      <li><svg width="8" height="11" viewBox="0 0 8 11"><rect x=".5" y="2" width="7" height="8" rx="1" fill="#ccc"/><rect x="2" y="0" width="4" height="3" fill="#ccc"/></svg><span>555 730 9261</span></li>
      <li><svg width="9" height="8" viewBox="0 0 9 8"><rect width="9" height="7" fill="#ccc"/><path d="M0 0l4.5 4L9 0" fill="none" stroke="#464646"/></svg><span>info@kova.com</span></li>
    </ul>
  </div>
  <div class="map" role="img" aria-label="Small street map showing the office location"></div>
  <div class="footer-links">
    <h4>Links</h4>
    <div class="cols">
      <ul><li>Home</li><li>Services</li><li>Team</li><li>Careers</li><li>Blog</li></ul>
      <ul><li>Contact us</li><li>Terms and conditions</li><li>Privacy Policy</li><li>Sitemap</li></ul>
    </div>
  </div>
  <div class="social">
    <h4>Social Media</h4>
    <div class="icons"><span></span><span></span><span></span><span></span></div>
  </div>
</footer>
<div class="footer-bottom">Copyright &copy; 2017 Company name. All rights reserved.</div>

</body>
</html>
```